Non fiction book cover. The book advises how to get a new job.

The book size will be 20cm high by 13cm wide and I need a front cover which can wrap around to the back. This book has a serious message, but I've tried to make it quite light to read and accessible. So I don't want a cover that is too dour or serious and not frivolous either. At the end of the project, I will need a high resolution 3D image of the book, included as part of the package.<br/>The Title of the book is:- "Past Sixty? Hunting for your final post?<br/>by Gareth Millbrook-Ashdown".<br/>I am thinking of a light yellow background, with a striking image to attract attention. The image and words should be clear and sharp.<br/>Here is the, BACK COVER wording.<br/>"This book tells you clearly and simply the steps that you need to take, to get a job, once you’re over 50.<br/>It advises you on the techniques to use to write a killer CV.<br/>It explains how to ensure that your CV attention.<br/>It shows the best way to approach your local job agency.<br/>It demonstrates the best way to use your network.<br/><br/>This book, written by someone with 30 years’ experience in the recruitment industry, gives you ALL the answers.<br/>Whether you are a top executive or someone after some local part time work, then this book is for you. <br/>With the help of this book you will secure your next position.<br/>

Target Market(s)

UK, over 50s, male and female.

Font styles to use
Serif

Colors
fbee3e

Requirements
Must have
• A clear uncluttered cover.
Should not have
• Fussy and over complicated

```html
<!DOCTYPE html>
<html lang="en">
<head>
<meta charset="utf-8">
<title>Past Sixty? Hunting for your final post? – Cover Spread</title>
<link href="https://fonts.googleapis.com/css2?family=Bebas+Neue&family=EB+Garamond:ital,wght@0,400;0,600;0,700;1,400;1,600&display=swap" rel="stylesheet">
<style>
  :root {
    --page-bg: #f1f1f1;
    --cover-yellow: #fbee3e;
    --title-teal: #2fa99a;
    --title-red: #d8303f;
    --ink: #222222;
    --art-teal: #3dbfa6;
    --art-pink: #e86b78;
  }
  * { box-sizing: border-box; margin: 0; padding: 0; }
  html, body {
    width: 1200px; height: 800px; overflow: hidden;
    background: var(--page-bg);
  }
  .canvas {
    width: 1200px; height: 800px;
    display: flex; align-items: center; justify-content: center;
  }
  .cover-spread {
    width: 1040px; height: 768px;
    background: var(--cover-yellow);
    display: flex;
    overflow: hidden;
    box-shadow: 0 6px 24px rgba(0,0,0,0.12);
  }
  .back-cover { width: 506px; position: relative; padding: 42px 34px 0 46px; }
  .spine {
    width: 40px; height: 768px; position: relative;
    display: flex; justify-content: center;
    padding-top: 44px; overflow: hidden;
  }
  .front-cover { width: 494px; position: relative; text-align: center; padding-top: 42px; }

  .kicker {
    font-family: 'EB Garamond', serif; font-weight: 400;
    color: var(--title-teal); line-height: 1;
  }
  .headline {
    font-family: 'Bebas Neue', sans-serif; font-weight: 400;
    color: var(--title-red); line-height: 0.92;
    text-shadow: 0 0 6px rgba(255,255,255,0.6);
  }

  .back-title { text-align: center; margin-bottom: 24px; }
  .back-title .kicker { font-size: 28px; }
  .back-title .headline { font-size: 42px; margin-top: 2px; }

  .blurb {
    font-family: 'EB Garamond', serif; font-size: 14.5px;
    color: var(--ink); line-height: 1.3;
  }
  .blurb p { margin-bottom: 16px; }
  .blurb ul { list-style: disc; padding-left: 40px; margin-bottom: 26px; }
  .blurb li { font-style: italic; font-weight: 600; font-size: 13.5px; margin-bottom: 14px; }

  .author {
    font-family: 'EB Garamond', serif; font-weight: 700;
    font-size: 27px; color: var(--ink); letter-spacing: 0.3px;
    text-transform: uppercase;
  }
  .front-title .kicker { font-size: 62px; margin-top: 10px; }
  .front-title .headline { font-size: 84px; margin-top: 4px; }

  .spine-text {
    writing-mode: vertical-rl;
    display: flex; align-items: center;
    white-space: nowrap;
  }
  .spine-text .kicker { font-size: 20px; }
  .spine-text .headline { font-size: 27px; margin-top: 6px; }
  .spine-text .spine-author {
    font-family: 'EB Garamond', serif; font-weight: 600;
    font-size: 16px; color: var(--ink); margin-top: 30px;
    text-transform: uppercase;
  }

  .artwork {
    position: absolute; bottom: 0;
    background: linear-gradient(160deg, var(--art-pink) 0%, var(--art-teal) 70%);
    opacity: 0.85;
  }
  .back-cover .artwork { left: 46px; width: 230px; height: 220px; }
  .front-cover .artwork { left: 40px; right: 40px; height: 330px; }
</style>
</head>
<body>
<main class="canvas">
  <section class="cover-spread" aria-label="Book cover wraparound">

    <article class="back-cover">
      <header class="back-title">
        <p class="kicker">PAST SIXTY?</p>
        <h2 class="headline">HUNTING FOR YOUR FINAL POST?</h2>
      </header>
      <div class="blurb">
        <p>This book tells you the steps that you need to take, to get a job once you’re over 50.</p>
        <ul>
          <li>It gives you all the tips you need to write a killer CV.</li>
          <li>It explains how ensure that your CV gets attention.</li>
          <li>It advises you how to approach your local job agency.</li>
          <li>It guides you through the steps you need to take to make effective use of your network.</li>
        </ul>
        <p>This book, written by someone with 30 years’ experience in the recruitment industry, gives you all the answers. Whether you are a top executive or someone after some local part time work, then this book is for you.</p>
        <p>It will help you to secure your next position.</p>
      </div>
      <div class="artwork" role="img" aria-label="Small illustration of a figure with a backpack sitting on top of a faceted teal and pink mountain beside clouds"></div>
    </article>

    <aside class="spine">
      <div class="spine-text">
        <span class="kicker">PAST SIXTY?</span>
        <span class="headline">HUNTING FOR YOUR FINAL POST?</span>
        <span class="spine-author">Gareth Millbrook-Ashdown</span>
      </div>
    </aside>

    <article class="front-cover">
      <p class="author">Gareth Millbrook-Ashdown</p>
      <header class="front-title">
        <p class="kicker">PAST SIXTY?</p>
        <h1 class="headline">HUNTING FOR<br>YOUR FINAL<br>POST?</h1>
      </header>
      <div class="artwork" role="img" aria-label="Illustration of a figure with a backpack and thought cloud sitting on the peak of a faceted teal and pink mountain, with pink and teal clouds"></div>
    </article>

  </section>
</main>
</body>
</html>
```